Website for BrightlineLabs presentation

We need a new website, ideally as a wordpress there, for BrightlineLabs - we focus on machine learning, big data, data science and data analytics. This website should have two main sections - team presentation, introduction and offered services as static pages, and a blog section.

Target Market(s)

Companies which would like to hire the consultants for data science

Industry/Entity Type

Data Service

Font styles to use
Sans Serif

Colors

Designer to choose colors to be used in the design.

Requirements
Must have
• Wordpress template, blog and presentation pages, nice background images, incorporate the existing logo from brief
Nice to have
• match the word and ppt existing templates for brightline labs

```html
<!DOCTYPE html>
<html lang="en">
<head>
<meta charset="utf-8">
<title>BrightlineLabs</title>
<link href="https://fonts.googleapis.com/css2?family=Lato:wght@300;400;700;900&display=swap" rel="stylesheet">
<style>
:root{
  --blue:#1787c4;
  --blue-light:#3ba6d8;
  --blue-deep:#0e5f8f;
  --navy:#07121f;
  --ink:#111;
  --grey:#666;
  --grey-light:#b8b8b8;
  --white:#fff;
}
*{box-sizing:border-box;margin:0;padding:0}
html,body{width:1200px;height:3093px;overflow:hidden}
body{font-family:'Lato',Arial,sans-serif;color:var(--ink);background:var(--white);position:relative}
.abs{position:absolute}
.btn{position:absolute;display:flex;align-items:center;justify-content:center;font-size:19px;letter-spacing:.5px;text-transform:uppercase}
.btn-white{background:var(--white);color:var(--ink)}
.btn-blue{background:var(--blue);color:var(--white)}
.accent{color:var(--blue)}

/* hero */
.hero{left:0;top:0;width:1200px;height:690px;overflow:hidden}
.hero-bg{position:absolute;inset:0;background:radial-gradient(circle at 78% 30%,#3b5d85 0%,#1b2e4a 30%,#0a1626 65%,#050b14 100%)}
.brand{left:78px;top:28px;display:flex;align-items:center;gap:14px;color:var(--white);font-weight:900;font-size:30px}
.brand-dot{width:34px;height:34px;border-radius:50%;background:var(--blue-light)}
.nav{top:56px;right:78px;display:flex;gap:66px;font-size:15px;color:#c9d3de;text-transform:uppercase}
.nav .active{color:var(--white)}
.hero-title{left:78px;top:275px;font-size:74px;font-weight:900;color:var(--white)}
.hero-text{left:80px;top:372px;width:500px;font-size:18px;line-height:25px;color:var(--white)}
.hero-wave{left:0;top:520px}

/* welcome */
.welcome-title{left:0;top:720px;width:1200px;text-align:center;font-size:50px;font-weight:900}
.welcome-text{left:170px;top:795px;width:860px;text-align:center;font-size:14px;line-height:23px;color:var(--grey)}

/* band */
.band{left:0;top:1000px;width:1200px;height:206px;background:linear-gradient(90deg,#3098cf,#45abdc)}
.band-kicker{left:110px;top:1052px;font-size:37px;font-weight:700;color:var(--ink)}
.band-title{left:110px;top:1098px;font-size:48px;font-weight:900;color:var(--white)}

/* services */
.services-title{left:0;top:1262px;width:1200px;text-align:center;font-size:50px;font-weight:900}
.service{top:1382px;width:248px;height:164px;border:1px solid #e2e2e2;border-radius:4px;text-align:center;padding-top:62px}
.service h3{font-size:19px;font-weight:700;color:#333;text-transform:uppercase}
.service p{margin:10px 22px 0;font-size:13px;line-height:19px;color:var(--grey-light)}
.service-icon{top:1341px;width:82px;height:82px;border-radius:50%;background:var(--blue-deep);display:flex;align-items:center;justify-content:center;border:4px solid #e8f2f8}

/* newsletter */
.newsletter{left:0;top:1612px;width:1200px;height:471px;background:linear-gradient(135deg,#0c1622,#15293c 50%,#0a1520)}
.newsletter-art{left:0;top:1640px;width:577px;height:443px;background:linear-gradient(160deg,#a9dbe9 0%,#6d5a8a 55%,#d8a04a 100%);opacity:.35}
.newsletter-kicker{left:604px;top:1740px;font-size:37px;font-weight:700;color:var(--blue-light)}
.newsletter-title{left:712px;top:1784px;font-size:46px;font-weight:700;color:var(--white)}
.newsletter-text{left:600px;top:1858px;width:520px;text-align:center;font-size:14px;line-height:21px;color:#d5dbe2}

/* news */
.news-title{left:0;top:2190px;width:1200px;text-align:center;font-size:50px;font-weight:900}
.news-img{top:2268px;width:417px;height:165px}
.news-img.one{background:linear-gradient(180deg,#0f2233,#2a6d98 50%,#0c1826)}
.news-img.two{background:radial-gradient(circle at 70% 50%,#3fc4f0 0%,#1d5a2a 35%,#08140c 90%)}
.news-head{top:2450px;font-size:21px;font-weight:900}
.news-date{top:2453px;font-size:15px;color:var(--grey)}
.news-text{top:2486px;width:400px;font-size:14px;line-height:21px;color:var(--grey)}

/* footer */
.footer{left:0;top:2560px;width:1200px;height:471px;background:linear-gradient(180deg,#0a1420,#111d2b)}
.footer-wave{left:0;top:2545px}
.footer-brand{left:78px;top:2700px;font-size:26px;font-weight:900;color:var(--white)}
.footer h4,.col-head{font-size:21px;font-weight:700;color:var(--white)}
.col{top:2780px;color:#e3e7ec;font-size:14px;line-height:21px}
.links{list-style:none}
.links li{line-height:31px}
.links li::before{content:"\2022";margin-right:10px;color:#aaa}
.contact-row{display:flex;gap:14px;margin-bottom:14px}
.contact-row svg{flex:none}
.field{position:absolute;border:1px solid #4a5563;font-size:12px;color:#9aa4ae;padding:10px 10px}
.copyright{left:0;top:3031px;width:1200px;height:62px;background:var(--blue-light);color:var(--ink);display:flex;align-items:center;justify-content:center;font-size:17px}
</style>
</head>
<body>

<section class="abs hero">
  <div class="hero-bg" role="img" aria-label="Background photo of a hand touching a glowing network globe over a night city"></div>
  <div class="abs brand"><span class="brand-dot"></span>BrightlineLabs</div>
  <nav class="abs nav"><span class="active">Home</span><span>About Us</span><span>Services</span><span>Blog</span><span>Contact Us</span></nav>
  <h1 class="abs hero-title">BIG DATA</h1>
  <p class="abs hero-text">Lorem Ipsum is simply dummy text of the printing and typesetting industry. Lorem Ipsum has been the industry's standard dummy text ever since the 1500s.</p>
  <a class="btn btn-white" style="left:78px;top:470px;width:186px;height:52px">Learn More</a>
  <svg class="abs hero-wave" width="1200" height="170" viewBox="0 0 1200 170">
    <path d="M0 105 C300 195 620 160 820 90 C960 40 1090 15 1200 30 V170 H0 Z" fill="#1787c4"/>
    <path d="M0 115 C300 190 620 175 860 110 C990 72 1100 55 1200 62 V170 H0 Z" fill="#fff"/>
    <path d="M0 108 C300 192 620 168 840 100" stroke="#c5c5c5" stroke-width="3" fill="none"/>
  </svg>
</section>

<h2 class="abs welcome-title">Welcome to <span class="accent">BRIGHTLINE LABS</span></h2>
<p class="abs welcome-text">Lorem Ipsum is simply dummy text of the printing and typesetting industry. Lorem Ipsum has been the industry's standard dummy text ever since the 1500s, when an unknown printer took a galley of type and scrambled it to make a type specimen book. It has survived not only five centuries, but also the leap into electronic typesetting, remaining essentially unchanged.</p>
<a class="btn btn-blue" style="left:507px;top:882px;width:186px;height:50px">Learn More</a>

<section class="abs band" role="img" aria-label="Blue band with faint binary digits"></section>
<p class="abs band-kicker">Make your team</p>
<p class="abs band-title">30% MORE PRODUCTIVE</p>
<a class="btn btn-white" style="left:792px;top:1074px;width:299px;height:54px;color:var(--blue);font-size:18px">Sign up for early access</a>

<h2 class="abs services-title">Our <span class="accent">SERVICES</span></h2>
<div class="abs service" style="left:78px"><h3>Machine Learning</h3><p>Lorem Ipsum is simply dummy text of the printing and typesetting industry.</p></div>
<div class="abs service" style="left:342px"><h3>Big Data</h3><p>Lorem Ipsum is simply dummy text of the printing and typesetting industry.</p></div>
<div class="abs service" style="left:608px"><h3>Data Science</h3><p>Lorem Ipsum is simply dummy text of the printing and typesetting industry.</p></div>
<div class="abs service" style="left:872px"><h3>Data Analytics</h3><p>Lorem Ipsum is simply dummy text of the printing and typesetting industry.</p></div>
<div class="abs service-icon" style="left:161px"><svg width="38" height="34" viewBox="0 0 38 34" fill="none" stroke="#fff" stroke-width="2"><rect x="2" y="2" width="34" height="22" rx="2"/><path d="M13 32h12M19 24v8M8 18l7-7 5 5 9-9"/></svg></div>
<div class="abs service-icon" style="left:426px"><svg width="34" height="36" viewBox="0 0 34 36" fill="none" stroke="#fff" stroke-width="2"><rect x="3" y="2" width="28" height="9" rx="2"/><rect x="3" y="13" width="28" height="9" rx="2"/><rect x="3" y="24" width="28" height="9" rx="2"/><circle cx="9" cy="6.5" r="1.5"/><circle cx="9" cy="17.5" r="1.5"/><circle cx="9" cy="28.5" r="1.5"/></svg></div>
<div class="abs service-icon" style="left:691px"><svg width="36" height="36" viewBox="0 0 36 36" fill="none" stroke="#fff" stroke-width="2"><rect x="9" y="9" width="18" height="18" rx="2"/><circle cx="18" cy="18" r="4"/><path d="M13 3v6M18 3v6M23 3v6M13 27v6M18 27v6M23 27v6M3 13h6M3 18h6M3 23h6M27 13h6M27 18h6M27 23h6"/></svg></div>
<div class="abs service-icon" style="left:955px"><svg width="36" height="34" viewBox="0 0 36 34" fill="none" stroke="#fff" stroke-width="2"><rect x="2" y="2" width="32" height="30" rx="2"/><path d="M2 9h32M8 26l7-8 5 4 8-9"/></svg></div>

<section class="abs newsletter" role="img" aria-label="Dark technology background"></section>
<div class="abs newsletter-art" role="img" aria-label="Illustration of a presenter beside a board, a robot and a dog"></div>
<p class="abs newsletter-kicker">We are always ready to help</p>
<h2 class="abs newsletter-title">NEWSLETTER</h2>
<p class="abs newsletter-text">Got a question? Our 24/7 support team will go the extra mile so you can have easy and enjoyable experience with us.</p>
<a class="btn btn-white" style="left:775px;top:1916px;width:174px;height:52px">Sign up now</a>

<h2 class="abs news-title">Latest <span class="accent">NEWS</span></h2>
<div class="abs news-img one" style="left:177px" role="img" aria-label="Photo of a server room corridor"></div>
<div class="abs news-img two" style="left:635px" role="img" aria-label="Photo of a glowing lab flask over green code"></div>
<p class="abs news-head" style="left:179px">Lorem Ipsum is simply.</p>
<p class="abs news-date" style="left:465px">Date : 15 Jun 2018</p>
<p class="abs news-text" style="left:179px">Lorem Ipsum is simply dummy text of the printing and typesetting industry.</p>
<p class="abs news-head" style="left:637px">Lorem Ipsum is simply.</p>
<p class="abs news-date" style="left:923px">Date : 15 Jun 2018</p>
<p class="abs news-text" style="left:637px">Lorem Ipsum is simply dummy text of the printing and typesetting industry.</p>

<footer class="abs footer" role="img" aria-label="Dark footer background with faint network pattern"></footer>
<svg class="abs footer-wave" width="1200" height="170" viewBox="0 0 1200 170">
  <path d="M0 0 H1200 V0 C1120 120 900 170 650 150 C520 140 480 120 430 110 H0 Z" fill="#fff"/>
  <path d="M430 110 C520 125 600 150 720 152 C950 160 1140 100 1200 0 V40 C1130 125 950 175 720 168 C600 165 520 140 430 110 Z" fill="#1c9ad6"/>
  <path d="M0 0 V30 H0 Z" fill="#fff"/>
</svg>
<div class="abs footer-brand">BrightlineLabs</div>
<div class="abs col" style="left:78px;width:170px"><p class="col-head" style="margin-bottom:20px">About Us</p><p>Lorem Ipsum is simply dummy text of the printing and typesetting industry.</p></div>
<div class="abs col" style="left:282px"><p class="col-head" style="margin-bottom:12px">Usefull Link</p><ul class="links"><li>Home</li><li>About</li><li>Services</li><li>Blog</li><li>Contact Us</li></ul></div>
<div class="abs col" style="left:485px;width:240px"><p class="col-head" style="margin-bottom:20px">Contact Info</p>
  <div class="contact-row"><svg width="18" height="22" viewBox="0 0 18 22"><path d="M9 1a8 8 0 0 0-8 8c0 6 8 12 8 12s8-6 8-12a8 8 0 0 0-8-8z" fill="#8a939c"/><circle cx="9" cy="9" r="3" fill="#111d2b"/></svg><span>123,Lorem Ipsum is simply dummy text of the printing.</span></div>
  <div class="contact-row"><svg width="18" height="18" viewBox="0 0 18 18"><path d="M4 1l3 4-2 2c1 2 3 4 5 5l2-2 4 3-2 3C8 16 2 10 1 4z" fill="#8a939c"/></svg><b>123 456 7878</b></div>
  <div class="contact-row"><svg width="18" height="18" viewBox="0 0 18 18"><rect x="1" y="5" width="16" height="11" rx="1" fill="#8a939c"/><rect x="4" y="1" width="10" height="5" fill="#8a939c"/></svg><span>123 456 7879</span></div>
  <div class="contact-row"><svg width="18" height="18" viewBox="0 0 18 18"><rect x="1" y="5" width="16" height="11" rx="1" fill="#8a939c"/><rect x="4" y="1" width="10" height="5" fill="#8a939c"/></svg><span>info@brightlinelabs.com</span></div>
</div>
<p class="abs col-head" style="left:753px;top:2780px">Keep In Touch</p>
<div class="field" style="left:753px;top:2825px;width:179px;height:37px">Enter Name</div>
<div class="field" style="left:940px;top:2825px;width:182px;height:37px">Enter Email</div>
<div class="field" style="left:753px;top:2866px;width:369px;height:62px">Message</div>
<a class="btn btn-white" style="left:753px;top:2936px;width:171px;height:50px">Sign up now</a>

<div class="abs copyright">©&nbsp;<b>BRIGHTLINE LABS</b>&nbsp;- 2018. All Rights Reserved.</div>

</body>
</html>
```